Business Card Design For A Cajun Seafood Restaurant

We are opening a cajun seafood restaurant in a week. We mainly serve cajun seafood which is orginally from Louisiana. We want design on both sides of a business card. I have menu on the website. You can go to www.reednkettle.example to check out our menu.

Restaurant name: Reed N' Kettle
Phone: +1 (555) 304-7712
Address: 48206 Ludlow Row, #7, Bexmoor Flats, Ca90000
Email: reednkettle@mailbox.example
Website: www.reednkettle.example

Maybe add social media icons (facebook, instagram) if looks nice on the business card.
facebook.com/reednkettle
instagram.com/reednkettle or @reednkettle

Attached is the logo and other business card samples that I like.

```html
<!DOCTYPE html>
<html lang="en">
<head>
<meta charset="utf-8">
<title>Reed N' Kettle – Business Card</title>
<link rel="stylesheet" href="https://fonts.googleapis.com/css2?family=Open+Sans:wght@400;600;800&display=swap">
<style>
  :root {
    --stage: #ece9e6;
    --card-orange: #ff6a00;
    --card-white: #f3f3f3;
    --band-grey: #4a4a4a;
    --text-light: #ffffff;
    --ink: #1c1c1c;
    --art-orange: #f07a2a;
    --art-yellow: #f2c200;
  }
  * { box-sizing: border-box; margin: 0; padding: 0; }
  html, body {
    width: 1200px; height: 900px; overflow: hidden;
    background: var(--stage);
    font-family: "Open Sans", Arial, sans-serif;
  }
  .canvas { position: relative; width: 1200px; height: 900px; }

  .card {
    position: absolute;
    box-shadow: 0 6px 18px rgba(0,0,0,0.18);
    overflow: hidden;
  }

  /* Front side */
  .card-front {
    left: 238px; top: 62px; width: 555px; height: 342px;
    background: var(--card-orange);
    color: var(--text-light);
  }
  .brand-name {
    position: absolute; left: 0; right: 0; top: 118px;
    text-align: center;
    font-weight: 800; font-size: 40px; letter-spacing: 1px;
    color: var(--ink);
  }
  .contact {
    position: absolute; left: 0; width: 535px; top: 168px;
    text-align: center; font-size: 14.5px; line-height: 19px;
  }
  .contact-row { display: flex; justify-content: center; align-items: center; gap: 6px; }
  .contact-row + .contact-row { margin-top: 0; }
  .contact-row .gap { width: 10px; }
  .contact .address { margin-top: 18px; }
  .contact .social { margin-top: 12px; }
  .icon { width: 12px; height: 12px; flex: none; fill: var(--text-light); }
  .social-mark { width: 12px; height: 12px; background: var(--text-light); border-radius: 2px; margin-right: 6px; }

  .mascot-front {
    position: absolute; left: 450px; top: 203px; width: 97px; height: 90px;
    border-radius: 45% 45% 30% 30%;
    background: radial-gradient(circle at 50% 45%, var(--art-yellow) 0 22%, var(--art-orange) 45%, var(--card-orange) 75%);
  }
  .pattern-band {
    position: absolute; left: 0; right: 0; bottom: 0; height: 50px;
    background: var(--band-grey);
  }

  /* Back side */
  .card-back {
    left: 457px; top: 518px; width: 560px; height: 344px;
    background: var(--card-white);
  }
  .mascot-back {
    position: absolute; left: 222px; top: 82px; width: 132px; height: 118px;
    border-radius: 45% 45% 30% 30%;
    background: radial-gradient(circle at 50% 40%, var(--art-yellow) 0 20%, var(--art-orange) 50%, #e86a1c 80%);
  }
  .card-back .brand-name {
    top: 208px; font-size: 36px; color: var(--ink);
  }
</style>
</head>
<body>
<main class="canvas">

  <section class="card card-front" aria-label="Business card front">
    <div class="brand-name">Reed N' Kettle</div>

    <div class="contact">
      <div class="contact-row">
        <svg class="icon" viewBox="0 0 24 24" aria-hidden="true"><path d="M6.6 10.8a15.5 15.5 0 0 0 6.6 6.6l2.2-2.2a1 1 0 0 1 1-.25 11.4 11.4 0 0 0 3.6.57 1 1 0 0 1 1 1V20a1 1 0 0 1-1 1A17 17 0 0 1 3 4a1 1 0 0 1 1-1h3.5a1 1 0 0 1 1 1c0 1.25.2 2.45.57 3.57a1 1 0 0 1-.25 1z"/></svg>
        <span>+1 (555) 304-7712</span>
        <span class="gap"></span>
        <svg class="icon" viewBox="0 0 24 24" aria-hidden="true"><path d="M2 5h20v14H2z M2 5l10 8 10-8" fill="none" stroke="#fff" stroke-width="2"/><path d="M2 6l10 7 10-7v-1H2z"/></svg>
        <span>reednkettle@mailbox.example</span>
      </div>
      <div class="contact-row">
        <svg class="icon" viewBox="0 0 24 24" aria-hidden="true"><circle cx="12" cy="12" r="10"/><path d="M2 12h20M12 2c3 3 3 17 0 20M12 2c-3 3-3 17 0 20" stroke="#ff6a00" stroke-width="1.5" fill="none"/></svg>
        <span>www.reednkettle.example</span>
      </div>
      <div class="contact-row address">48206 Ludlow Row, #7, Bexmoor Flats, Ca90000</div>
      <div class="contact-row social">
        <span class="social-mark" aria-hidden="true"></span>
        <span>reednkettle</span>
      </div>
    </div>

    <div class="mascot-front" role="img" aria-label="Mascot illustration: cartoon crab holding an ear of corn"></div>
    <div class="pattern-band" role="img" aria-label="Decorative grey shell pattern band"></div>
  </section>

  <section class="card card-back" aria-label="Business card back">
    <div class="mascot-back" role="img" aria-label="Mascot illustration: cartoon crab holding an ear of corn"></div>
    <div class="brand-name">Reed N' Kettle</div>
  </section>

</main>
</body>
</html>
```